SaaS Early tech startup business card design

Unique design for experience ecommerce platform company. the business cards will be used by executive members. conformance with color code is required.

```html
<!DOCTYPE html>
<html lang="en">
<head>
<meta charset="utf-8">
<title>Velto business card</title>
<link href="https://fonts.googleapis.com/css2?family=Montserrat:wght@800&family=Roboto:wght@400&display=swap" rel="stylesheet">
<style>
  :root {
    --backdrop: #6b6869;
    --navy: #1f2540;
    --navy-glow: #243050;
    --paper: #f7f7f5;
    --teal-deep: #135a6b;
    --teal: #14807f;
    --ink: #1c1c1c;
    --white: #ffffff;
  }
  * { margin: 0; padding: 0; box-sizing: border-box; }
  html, body { width: 1200px; height: 1200px; overflow: hidden; }
  body { background: var(--backdrop); position: relative; font-family: "Roboto", sans-serif; }

  .card {
    position: absolute;
    width: 348px;
    height: 594px;
    border-radius: 22px;
    overflow: hidden;
  }
  .card--front { left: 200px; top: 298px; background: var(--navy); color: var(--white); }
  .card--back { left: 637px; top: 292px; background: var(--paper); color: var(--ink); text-align: center; }

  .card__texture {
    position: absolute; inset: 0;
    background: radial-gradient(ellipse at 50% 15%, var(--navy-glow) 0%, transparent 55%),
                radial-gradient(ellipse at 50% 85%, var(--navy-glow) 0%, transparent 55%),
                var(--navy);
  }

  .front-brand { position: absolute; left: 0; right: 0; top: 242px; text-align: center; }
  .front-brand__name {
    font-family: "Montserrat", sans-serif; font-weight: 800;
    font-size: 84px; line-height: 1; letter-spacing: -1px; color: var(--white);
  }
  .front-brand__tagline {
    margin-top: 4px; font-size: 15px; letter-spacing: 5.6px; text-transform: uppercase;
    padding-left: 5px;
  }

  .back-brand { position: absolute; left: 0; right: 0; top: 52px; }
  .back-brand__name {
    font-family: "Montserrat", sans-serif; font-weight: 800;
    font-size: 84px; line-height: 1; letter-spacing: -1px; color: var(--teal);
  }
  .back-brand__tagline { margin-top: 8px; font-size: 16px; letter-spacing: 1.4px; }

  .holder { position: absolute; left: 0; right: 0; top: 270px; }
  .holder__name {
    font-family: "Montserrat", sans-serif; font-weight: 800;
    font-size: 38px; line-height: 1.1; color: var(--teal-deep);
  }

  .contact { position: absolute; left: 0; right: 0; top: 327px; font-size: 16.5px; line-height: 24px; }
  .contact__row { display: flex; justify-content: center; align-items: center; gap: 7px; }
  .contact__icon { width: 14px; height: 14px; fill: none; stroke: var(--teal); stroke-width: 1.6; }
  .contact__gap { width: 4px; }

  .address { position: absolute; left: 0; right: 0; top: 402px; font-size: 16.5px; line-height: 24px; font-style: normal; }

  .social { position: absolute; left: 0; right: 0; top: 542px; font-size: 16px;
    display: flex; justify-content: center; align-items: center; gap: 7px; }
  .social__dot { width: 14px; height: 14px; border-radius: 50%; background: var(--teal-deep); }
</style>
</head>
<body>

<section class="card card--front">
  <div class="card__texture" role="img" aria-label="Faint wave line texture on navy background"></div>
  <div class="front-brand">
    <div class="front-brand__name">velto</div>
    <div class="front-brand__tagline">Made around you</div>
  </div>
</section>

<section class="card card--back">
  <div class="back-brand">
    <div class="back-brand__name">velto</div>
    <div class="back-brand__tagline">Made around you</div>
  </div>

  <div class="holder"><h1 class="holder__name">Rami K.</h1></div>

  <div class="contact">
    <div class="contact__row">
      <svg class="contact__icon" viewBox="0 0 16 16"><path d="M2 6c0-2 2-3 6-3s6 1 6 3l-2 1-1-2H5L4 7z" fill="var(--teal)"/><rect x="4" y="8" width="8" height="5" rx="1" fill="var(--teal)"/></svg>
      <span>(00) 0111 VELTO</span>
    </div>
    <div class="contact__row">
      <svg class="contact__icon" viewBox="0 0 16 16"><rect x="1.5" y="3.5" width="13" height="9"/><path d="M1.5 3.5 8 9l6.5-5.5M1.5 12.5 6 7.5M14.5 12.5 10 7.5"/></svg>
      <span>info@velto.net</span>
      <span class="contact__gap"></span>
      <svg class="contact__icon" viewBox="0 0 16 16"><circle cx="8" cy="8" r="6.2"/><ellipse cx="8" cy="8" rx="2.6" ry="6.2"/><path d="M1.8 8h12.4M3 4.8h10M3 11.2h10"/></svg>
      <span>velto.net</span>
    </div>
  </div>

  <address class="address">
    Meridian Tower, Dubai<br>
    Dubai Tech Park, UAE
  </address>

  <div class="social">
    <span class="social__dot"></span>
    <span>/getvelto</span>
  </div>
</section>

</body>
</html>
```